OpenHarbor Yoga Website Design

Business Logo - attached
5 pages being:
Home
About
Classes
Blog
Contact

Would like Scrolling webpage and yoga symbols to be used.

Must have's being:
Easy to navigate, Text needs to be able to be edited/updated, Enquire Now Links, More Information Links, be a secure site, SEO,

Please refer to attached document for the information for the body of the website.

Target Market(s)

Educators, Community Service, Health and Wellbeing, Mental Health

Industry/Entity Type

Yoga

Coding

Coded - Design and coding required

Number of Pages Required

5+ page

Font styles to use
Other font styles liked:
• Bella Bold BC

Colors
0094D4
00A9DD
6FCCEA
C7EBF8
E9F6FB
6B429C
8869AF
B7A5CE
E3DAEB
F3F0F8

Requirements
Must have
• Easy to navigate, Text needs to be able to be edited/updated, Enquire Now Links, More Information Links, be a secure site, SEO,
Nice to have
• Scrolling webpage, yoga symbols

```html
<!DOCTYPE html>
<html lang="en">
<head>
<meta charset="utf-8">
<title>OpenHarbor Yoga – Website Pages</title>
<link href="https://fonts.googleapis.com/css2?family=Arimo:wght@400;700&family=Kaushan+Script&family=Playfair+Display:wght@400;700&display=swap" rel="stylesheet">
<style>
:root{
  --board:#ae8fe1;
  --purple:#6b429c;
  --purple-deep:#5a3597;
  --purple-mid:#8869af;
  --lilac:#b7a5ce;
  --lilac-pale:#e3daeb;
  --teal:#22c2da;
  --cyan:#00a9dd;
  --blue:#0094d4;
  --band:#22b7d5;
  --magenta:#9c4aa0;
  --footer:#4f408e;
  --grey:#f2f2f5;
  --ink:#444;
  --title-ink:#3b2e8e;
  --white:#fff;
}
*{margin:0;padding:0;box-sizing:border-box}
html,body{width:1037px;height:1200px;overflow:hidden;background:var(--board)}
body{font-family:"Arimo",Arial,sans-serif;color:var(--ink)}
.board{position:absolute;left:0;top:0;width:1790px;height:2072px;transform:scale(.57933);transform-origin:0 0;background:var(--board)}
.col-title{position:absolute;top:48px;width:344px;text-align:center;color:var(--white);font-size:19px}
.page{position:absolute;top:95px;width:344px;background:var(--white);overflow:hidden}
.a{position:absolute}
.topbar{position:absolute;left:0;top:0;width:100%;height:15px;background:linear-gradient(90deg,#4b3795,#1aa2c3 55%,#5a3b98);color:var(--white);font-size:4.5px;display:flex;justify-content:flex-end;align-items:center;gap:6px;padding-right:36px;white-space:nowrap}
.topbar .dot{width:5px;height:5px;border-radius:50%;background:var(--white)}
.nav{position:absolute;left:0;top:15px;width:100%;height:30px;background:var(--white);display:flex;align-items:center;padding:0 22px 0 36px;white-space:nowrap}
.brand{display:flex;align-items:center;gap:3px;font-size:4.5px;color:var(--purple);font-weight:700;flex-shrink:0}
.brand i{width:12px;height:12px;border-radius:50%;border:1px solid var(--lilac);display:block}
.menu{display:flex;gap:13px;margin-left:auto;margin-right:10px;font-family:"Playfair Display",serif;font-size:5px;color:#333;flex-shrink:0}
.menu span{white-space:nowrap}
.menu span.on{border-bottom:1.5px solid var(--purple);padding-bottom:3px;color:var(--purple)}
.pill{display:inline-block;border-radius:20px;background:linear-gradient(90deg,var(--purple-deep),var(--cyan));color:var(--white);font-family:"Playfair Display",serif;font-size:4.5px;padding:3px 7px;font-weight:700;white-space:nowrap;flex-shrink:0}
.hero{position:absolute;left:0;top:45px;width:100%;background:linear-gradient(180deg,#5a3598 0%,#4c52b4 45%,#28c6db 100%);color:var(--white)}
.hero-mark{position:absolute;left:30px;width:110px;height:110px;border-radius:50%;background:rgba(255,255,255,.14);display:flex;align-items:center;justify-content:center;text-align:center;font-size:8px;color:var(--lilac-pale);font-weight:700}
.hero h1{position:absolute;left:200px;font-family:"Kaushan Script",cursive;font-weight:400;font-size:16px;white-space:nowrap}
.script{font-family:"Kaushan Script",cursive;font-weight:400}
.photo{position:absolute;border-radius:1px}
.p-warm{background:linear-gradient(135deg,#e8ddd2,#b79c86)}
.p-room{background:linear-gradient(135deg,#dfe3e6,#9aa7b3)}
.p-kids{background:linear-gradient(135deg,#f0c9a9,#76a4cf)}
.p-bright{background:linear-gradient(135deg,#f08b7a,#6fb48a 60%,#4a7fc4)}
.p-dark{background:linear-gradient(135deg,#49504a,#2a2f2b)}
.p-mat{background:linear-gradient(135deg,#cfd8e8,#e8a7b5)}
.p-online{background:linear-gradient(135deg,#e3e6ef,#7ea0c9)}
.frame{position:absolute}
.txt{position:absolute;font-size:4.4px;line-height:1.45;color:var(--ink)}
.txt p+p{margin-top:4px}
.h-sec{position:absolute;font-family:"Kaushan Script",cursive;font-size:13.5px;color:var(--purple-deep);white-space:nowrap}
.h-sub{position:absolute;font-family:"Kaushan Script",cursive;font-size:11px;white-space:nowrap}
.list{position:absolute;list-style:none;font-size:4.4px;line-height:1;color:var(--ink)}
.list li{position:relative;padding-left:8px;margin-bottom:4.2px}
.list li::before{content:"";position:absolute;left:0;top:0;border-left:2.8px solid transparent;border-right:2.8px solid transparent;border-bottom:4px solid var(--lilac)}
.center{text-align:center}
.band{position:absolute;left:0;width:100%}
.field{position:absolute;font-size:4.5px;color:#555;border-bottom:.6px solid #ccc;padding-bottom:6px}
.footer{position:absolute;left:0;width:100%;height:110px;background:var(--footer);color:var(--white)}
.footer h4{position:absolute;top:18px;font-family:"Kaushan Script",cursive;font-weight:400;font-size:8px;white-space:nowrap}
.footer ul{position:absolute;top:33px;list-style:none;font-size:4.3px;line-height:1.95;white-space:nowrap}
.footer ul li::before{content:"";display:inline-block;width:3px;height:3px;border-radius:50%;background:var(--white);margin-right:3px;vertical-align:middle}
.f-mark{position:absolute;left:150px;top:18px;width:44px;height:44px;border-radius:50%;border:1px solid var(--lilac);display:flex;align-items:center;justify-content:center;text-align:center;font-size:5px;color:var(--lilac-pale)}
.footer .rule{position:absolute;left:36px;right:36px;top:82px;border-top:.6px solid rgba(255,255,255,.25)}
.footer .copy{position:absolute;left:0;width:100%;top:92px;text-align:center;font-size:4.4px}
.cost{position:absolute;border-radius:0 8px 8px 0;color:var(--white);font-size:4.3px;font-weight:700;padding:3px 6px;line-height:1.3}
.btn{position:absolute;border-radius:20px;color:var(--white);font-family:"Playfair Display",serif;font-weight:700;font-size:4.6px;padding:3px 8px;white-space:nowrap;background:linear-gradient(90deg,var(--purple-deep),var(--purple-mid))}
.btn.cy{background:linear-gradient(90deg,var(--cyan),var(--teal))}
.btn.dk{background:linear-gradient(90deg,#2c2f8f,#3a67c2)}
.card{position:absolute;background:var(--white);box-shadow:0 0 3px rgba(0,0,0,.08)}
.card h3{position:absolute;font-size:6.6px;line-height:1.25;color:var(--title-ink);font-weight:700}
.meta{position:absolute;font-size:3.8px;color:#666;white-space:nowrap}
.avatar{position:absolute;width:18px;height:18px;border-radius:50%;background:#c9c9cf}
.by{position:absolute;font-size:3.8px;color:#999;line-height:1.3;white-space:nowrap}
.by b{color:var(--blue);font-size:4.3px}
.side h5{position:absolute;font-family:"Kaushan Script",cursive;font-weight:400;font-size:9px;color:var(--title-ink);white-space:nowrap}
.rp{position:absolute;width:84px;height:24px}
.rp .photo{left:0;top:0;width:24px;height:22px}
.rp div.t{position:absolute;left:28px;top:0;font-size:3.5px;line-height:1.35;color:var(--title-ink);font-weight:700}
.rp div.t span{color:var(--cyan);display:block;margin-top:2px}
.ad-cap{position:absolute;left:0;bottom:0;width:100%;height:34px;background:linear-gradient(0deg,#6b2fc2,#8a4fd6);color:var(--white);font-family:"Kaushan Script",cursive;font-size:5px;text-align:center;padding:6px 5px;line-height:1.2}
.share{position:absolute;width:12px;height:12px;border-radius:50%}
.input{position:absolute;border:.6px solid #ccc;font-size:3.6px;color:#777;padding:2px 3px}
</style>
</head>
<body>
<div class="board">

  <div class="col-title" style="left:102px">Home Page</div>
  <div class="col-title" style="left:516px">Classes Page Sample 2</div>
  <div class="col-title" style="left:930px">Blog Page Sample 2</div>
  <div class="col-title" style="left:1344px">Single Blog Page Sample 2</div>

  <!-- HOME -->
  <section class="page" style="left:102px;height:1329px">
    <div class="topbar"><span>info@openharboryoga.com.au</span><span>Call Us: 0491 570 156</span><i class="dot"></i><i class="dot"></i></div>
    <nav class="nav"><div class="brand"><i></i>OpenHarbor Yoga</div><div class="menu"><span class="on">Home</span><span>About</span><span>Classes</span><span>Blog</span><span>Contact</span></div><span class="pill">Enquire Now</span></nav>
    <header class="hero" style="height:166px">
      <div class="hero-mark" style="top:28px">OpenHarbor Yoga</div>
      <h1 style="top:56px">OpenHarbor Yoga</h1>
      <span class="pill a" style="left:231px;top:87px;border:1px solid #fff;font-size:5.5px;padding:3px 8px">Enquire Now</span>
    </header>

    <h2 class="h-sec center" style="left:0;width:344px;top:230px">Welcome to OpenHarbor Yoga...</h2>
    <div class="frame" style="left:26px;top:333px;width:58px;height:52px;border:.8px solid var(--lilac)"></div>
    <div class="photo p-warm" role="img" aria-label="Woman meditating cross-legged on a yoga mat" style="left:36px;top:267px;width:120px;height:109px"></div>
    <div class="txt" style="left:162px;top:267px;width:138px">
      <p>OpenHarbor Yoga believe that you are never too young to benefit from and fall in love with yoga. My aim is to EMPOWER kids and teens to thrive by teaching life skills in Yoga, Mindfulness and Breathing techniques to deal with daily challenges and big emotions.</p>
      <p>OpenHarbor Yoga gives kids an opportunity to enjoy and experience yoga for themselves and primarily focuses on programs for Schools, Pre Schools and Early Learning Centres, Private Classes, Sporting Clubs, Martial Arts Schools, Scout Groups and Occupational Therapy Centres just to name a few. All classes are age appropriate and encourage children's natural drive to learn, move, and be creative.</p>
    </div>
    <span class="btn" style="left:165px;top:362px">More Information</span>

    <div class="band" style="top:408px;height:112px;background:var(--band)"></div>
    <h2 class="h-sec center" style="left:0;width:344px;top:432px;color:#fff">Benefits of Yoga...</h2>
    <p class="txt center" style="left:66px;top:458px;width:212px;color:#fff">The benefits of yoga can last a lifetime. It is my aim &amp; passion to introduce yoga to kids of all ages and backgrounds so that they can not only experience the benefits of yoga but fall in love with the practice.</p>
    <h3 class="h-sub center" style="left:0;width:344px;top:485px;color:#fff;font-size:10px">Yoga benefits include:</h3>

    <h3 class="h-sub" style="left:37px;top:550px;color:var(--purple)">Healthy Bodies</h3>
    <ul class="list" style="left:37px;top:572px;width:128px">
      <li>Develops strong, flexible and healthy bodies</li><li>Promotes spinal alignment and good posture</li><li>Builds energy and stamina</li><li>Improves internal physical function - organs, digestion, elimination, circulation, and blood flow.</li><li>Helps breathing and lung capacity</li><li>Teaches the enjoyment of movement</li><li>Works the 'whole' body</li>
    </ul>
    <div class="frame" style="left:178px;top:566px;width:139px;height:93px;border-right:4px solid var(--purple-deep);border-bottom:4px solid var(--purple-deep)"></div>
    <div class="photo p-room" role="img" aria-label="Child and adult doing downward dog in a bright room" style="left:168px;top:556px;width:140px;height:94px"></div>

    <div class="frame" style="left:18px;top:690px;width:141px;height:97px;border-left:4px solid var(--purple-deep);border-bottom:4px solid var(--purple-deep)"></div>
    <div class="photo p-kids" role="img" aria-label="Group of children sitting in yoga poses with arms raised" style="left:26px;top:684px;width:140px;height:94px"></div>
    <h3 class="h-sub" style="left:188px;top:692px;color:var(--cyan)">Healthy Minds</h3>
    <ul class="list" style="left:188px;top:714px;width:140px">
      <li>Cultivates confidence and self-esteem</li><li>Develops concentration and attention</li><li>Clears the mind for better clarity and decision making</li><li>Helps relax and sleep better</li><li>Calms the nervous system</li><li>Learns to cope with stressful situations</li><li>Balances emotions</li>
    </ul>

    <h3 class="h-sub" style="left:37px;top:818px;color:var(--cyan)">Healthy Spirits</h3>
    <ul class="list" style="left:37px;top:840px;width:120px">
      <li>Fosters creativity, expression and imagination</li><li>Cultivates kindness to themselves and others</li><li>Cultivates respect for self and others</li><li>Builds balance and inner quiet</li><li>Builds inner strength and resilience</li><li>Teaches self-awareness</li><li>Focuses on positive self-talk</li>
    </ul>
    <div class="frame" style="left:173px;top:834px;width:140px;height:95px;border-right:4px solid var(--teal);border-bottom:4px solid var(--teal)"></div>
    <div class="photo p-warm" role="img" aria-label="Adults practising yoga poses on mats in a studio" style="left:163px;top:824px;width:140px;height:96px"></div>

    <div class="txt center" style="left:50px;top:960px;width:244px">
      <p>OpenHarbor Yoga combines all the benefits of traditional yoga and a lot of fun! We play games and practice engaging flows which get our bodies moving, then we take a quiet moment to be still and calm as we focus on our breathing.</p>
      <p>OpenHarbor Yoga Kids will learn that relaxation is just as important as moving their bodies, and the exercises which they learn in class can easily be repeated at any time in their busy day to feel calm and grounded.</p>
    </div>

    <div class="band" style="top:1040px;height:178px;background:#fff"></div>
    <h2 class="h-sec center" style="left:0;width:344px;top:1073px;font-size:16px">Contact Us</h2>
    <div class="field" style="left:57px;top:1105px;width:110px">Name:</div>
    <div class="field" style="left:176px;top:1105px;width:110px">Phone:</div>
    <div class="field" style="left:57px;top:1126px;width:110px">Email:</div>
    <div class="field" style="left:176px;top:1126px;width:110px">Subject:</div>
    <div class="field" style="left:57px;top:1147px;width:229px;padding-bottom:20px">Message:</div>
    <span class="btn" style="left:148px;top:1180px">Submit Now</span>

    <footer class="footer" style="top:1218px">
      <h4 style="left:37px">Contact Us</h4>
      <ul style="left:37px"><li>Contact: Dana Whitfield</li><li>Phone: 0491 570 156</li><li>Email: info@openharboryoga.com.au</li><li>Location: Fernvale, Victoria Australia 3999</li></ul>
      <div class="f-mark">OpenHarbor Yoga</div>
      <h4 style="left:213px">Connect With Us</h4>
      <ul style="left:213px"><li>Facebook: OpenHarbor Yoga | Facebook</li><li>Instagram: openharboryoga4kids</li><li style="margin-top:4px">ABN: 12 345 678 901</li></ul>
      <div class="rule"></div><div class="copy">Copyright 2023 OpenHarbor Yoga</div>
    </footer>
  </section>

  <!-- CLASSES -->
  <section class="page" style="left:516px;height:1823px">
    <div class="topbar"><span>info@openharboryoga.com.au</span><span>Call Us: 0491 570 156</span><i class="dot"></i><i class="dot"></i></div>
    <nav class="nav"><div class="brand"><i></i>OpenHarbor Yoga</div><div class="menu"><span>Home</span><span>About</span><span class="on">Classes</span><span>Blog</span><span>Contact</span></div><span class="pill">Enquire Now</span></nav>
    <header class="hero" style="height:132px">
      <div class="hero-mark" style="top:14px;left:50px;width:100px;height:100px">OpenHarbor Yoga</div>
      <h1 style="top:54px;left:172px">Yoga Classes...</h1>
    </header>

    <h2 class="h-sec center" style="left:0;width:344px;top:195px">OpenHarbor Kids Yoga Classes...</h2>
    <p class="txt center" style="left:70px;top:222px;width:204px;font-size:5px">Does your child or teen get anxious? Would they benefit from activities that help to build resilience, without competition or pressure?</p>
    <h4 class="a" style="left:37px;top:260px;width:125px;font-size:5.4px;color:var(--purple-deep);line-height:1.25">OpenHarbor Yoga offers a range of options of classes for kids and teens:</h4>
    <ul class="list" style="left:37px;top:281px;width:128px"><li>after school classes (Day and Location)</li><li>day care/ early learning (age 2- preschool)</li><li>school (as part of the curriculum)</li><li>private sessions (in person at Location)</li></ul>
    <h4 class="a" style="left:37px;top:327px;width:115px;font-size:5.4px;color:var(--cyan);line-height:1.25">Classes are a perfect blend of fun + calm and include:</h4>
    <ul class="list" style="left:37px;top:348px;width:132px"><li>mindful movements</li><li>stretches to improve flexibility</li><li>exercises to help build strength, co-ordination &amp; good posture</li><li>fun group activities and games to enhance teamwork; social skills; playfulness &amp; conscious communication</li><li>calm breathing techniques</li><li>mindfulness activities</li><li>guided relaxation to reduce anxiety</li></ul>
    <p class="txt" style="left:37px;top:429px;width:118px">Classes are tailored to meet the unique needs of the group to be age appropriate and suitable for their capability.</p>
    <div class="frame" style="left:167px;top:272px;width:40px;height:72px;border-left:4px solid var(--purple-deep);border-top:4px solid var(--purple-deep)"></div>
    <div class="photo p-kids" role="img" aria-label="Two children stretching on mats" style="left:172px;top:277px;width:64px;height:67px"></div>
    <div class="photo p-room" role="img" aria-label="Girl doing a seated forward stretch" style="left:243px;top:277px;width:64px;height:67px"></div>
    <div class="frame" style="left:270px;top:400px;width:40px;height:42px;border-right:4px solid var(--purple-deep);border-bottom:4px solid var(--purple-deep)"></div>
    <div class="photo p-kids" role="img" aria-label="Children in a line doing a standing yoga pose" style="left:174px;top:349px;width:133px;height:89px"></div>

    <div class="band" style="top:475px;height:320px;background:var(--grey)"></div>
    <div class="photo p-bright" role="img" aria-label="Colourful number magnets on a board" style="left:36px;top:505px;width:138px;height:91px"></div>
    <h3 class="h-sub" style="left:182px;top:502px;color:var(--purple-deep);font-size:9.5px">Yoga in Early Learning ...</h3>
    <p class="a" style="left:182px;top:523px;width:130px;font-size:4.8px;font-weight:700;color:#222;line-height:1.3">Offer OpenHarbor Yoga at your childcare centre or Kindergarten!</p>
    <div class="txt" style="left:182px;top:544px;width:130px;font-size:4px">
      <p>Give little ones a way to let out their energy in a healthy and mindful environment. OpenHarbor Yoga's experienced kids and teens yoga teacher teach children to have fun with yoga, build strength, focus, balance and coordination in a kind and nurturing way.</p>
      <p>Yoga sessions can be tailored for the different ages of children, group size, curriculum strand / themes in the centre; weekly program, or one-off class. We bring yoga to you and Catering for the whole centre.</p>
    </div>
    <ul class="list" style="left:182px;top:608px"><li>15 min classes with ages 2-3</li><li>20 min class with ages 3-4</li><li>30 min class with ages 4-5</li></ul>
    <div class="cost" style="left:182px;top:638px;width:122px;background:linear-gradient(90deg,var(--cyan),var(--teal))">Costs: from $90- $180 depending on location, duration, mats, class sizes</div>
    <h3 class="h-sub" style="left:36px;top:648px;color:var(--purple)">Yoga in Schools...</h3>
    <p class="a script" style="left:36px;top:672px;font-size:7px;color:#222;white-space:nowrap">Offer OpenHarbor Yoga at your school!</p>
    <div class="txt" style="left:36px;top:686px;width:130px;font-size:4px">
      <p>Classes are tailored by the age of students, group size, curriculum strand / made relevant to a subject, term program or one-off class for both Primary and High Schools. We bring yoga to you...options include after school yoga club, yoga as a PE unit, yoga in health class, and more.</p>
      <p>Experienced kids and teens yoga teacher that engage kids with thoughtful yoga classes that develop strength, focus, confidence and more. Balanced with time to breathe and reset. Online Classes are also available</p>
    </div>
    <div class="cost" style="left:36px;top:750px;width:122px;background:linear-gradient(90deg,var(--purple-deep),var(--purple-mid))">Costs: from $120- $200 depending on location, duration, mats, and class size.</div>
    <div class="photo p-dark" role="img" aria-label="Stack of books, pencils and an apple on a school desk" style="left:179px;top:685px;width:127px;height:80px"></div>

    <div class="photo p-warm" role="img" aria-label="Young person meditating on a mat" style="left:34px;top:817px;width:135px;height:130px"></div>
    <h3 class="h-sub" style="left:181px;top:815px;color:var(--cyan);font-size:9.5px">Yoga for Tweens (aged 7-11)...</h3>
    <p class="txt" style="left:181px;top:834px;width:122px;font-size:3.9px">An interactive 60-minute class for children aged 7-11 to enjoy yoga poses; games; partner yoga and learning life skills in a fun way. Each class ends with quiet time to breathe and relax</p>
    <div class="txt" style="left:181px;top:862px;width:60px;font-size:4px"><b>When:</b><br>Day &amp; Time<br>Term: Aug 20- Sept 7</div>
    <div class="txt" style="left:241px;top:862px;font-size:4px"><b>Where:</b><br>TBC</div>
    <div class="txt" style="left:181px;top:893px;font-size:4px;font-weight:700"><span>Cost:</span><br>$55 4 class pass<br>$110 term pass<br>$170 term pass for 2 siblings<br>No credits for missed classes</div>
    <span class="btn dk" style="left:181px;top:930px">Book Now</span>
    <div class="photo p-mat" role="img" aria-label="Teen girls and instructor practising yoga on pink mats" style="left:34px;top:968px;width:135px;height:135px"></div>
    <h3 class="h-sub" style="left:181px;top:966px;color:var(--cyan);font-size:9.5px">Yoga for Teen Girls...</h3>
    <div class="txt" style="left:181px;top:985px;width:122px;font-size:3.9px"><p>A beautiful class for teen girls to learn life skills and build self-confidence through yoga poses and empowering affirmations and partner yoga. Each class ends with quiet time to breathe and relax.</p><p>If your daughter is not yet a teen, but is in high school, she can join.</p></div>
    <div class="txt" style="left:181px;top:1033px;width:60px;font-size:4px"><b>When:</b><br>Thursday, 5-6pm<br>Term 3: July 20- Sept 7</div>
    <div class="txt" style="left:241px;top:1033px;font-size:4px"><b>Where:</b><br>TBC</div>
    <div class="txt" style="left:181px;top:1064px;font-size:4px;font-weight:700">Cost:<br>$60 4 class pass<br>$120 term pass<br>$190 term pass for 2 siblings<br>No credits for missed classes</div>
    <span class="btn dk" style="left:181px;top:1101px">Book Now</span>

    <div class="band" style="top:1148px;height:135px;background:linear-gradient(180deg,#5a3598,#4c64bd 55%,#2ac4da)"></div>
    <h2 class="h-sec center" style="left:0;width:344px;top:1166px;color:#fff;font-size:12px">Private Sessions...</h2>
    <div class="txt center" style="left:78px;top:1190px;width:188px;color:#fff;font-size:3.9px">
      <p>If a group class is not suitable for your child, or if they would benefit from an individualised program to suit their needs, then you can consider a private lesson.</p>
      <p>As a Kids Yoga Teacher, I have a Working with Children's Check card, first aid certificate, insurance, and relevant qualifications.</p>
      <p>One on one, private sessions are the most effective way to ensure the student receives exactly what is right for them in the moment.</p>
    </div>
    <span class="pill a" style="left:148px;top:1245px;border:1px solid #fff">Enquire Now</span>

    <div class="band" style="top:1283px;height:129px;background:var(--magenta)"></div>
    <div class="photo p-online" role="img" aria-label="Child doing yoga on a mat in front of a laptop" style="left:34px;top:1307px;width:128px;height:79px"></div>
    <h3 class="h-sub" style="left:183px;top:1320px;color:#fff">Kids Yoga Online</h3>
    <p class="txt" style="left:183px;top:1343px;width:110px;color:#fff;font-size:3.9px">"Online" is the new world we live in... and whilst it is not my favourite way to connect, it is better than no connection at all.... So, if face to face sessions with me aren't possible, check out these options.</p>

    <h3 class="h-sub" style="left:35px;top:1440px;color:var(--purple);font-size:9.5px">Online private sessions for kids</h3>
    <p class="txt" style="left:35px;top:1460px;width:112px;font-size:3.9px">Online private sessions on zoom are designed for kids who physically cannot make it to a yoga class, either due to distance, anxiety, or medical reasons. I will tailor the activities and duration (30-60 mins) to suit their individual needs.</p>
    <p class="a" style="left:35px;top:1496px;width:120px;font-size:4.6px;font-weight:700;color:#222;line-height:1.3">Yes! I want my child to learn calm tools in a tailored, online private session</p>
    <span class="btn" style="left:35px;top:1516px">Enquire Now</span>
    <div class="photo p-room" role="img" aria-label="Children doing a side stretch pose indoors" style="left:170px;top:1437px;width:137px;height:91px"></div>
    <div class="photo p-bright" role="img" aria-label="Class of children doing yoga outdoors on the grass" style="left:33px;top:1558px;width:137px;height:121px"></div>
    <h3 class="h-sub" style="left:183px;top:1555px;color:var(--purple);font-size:9.5px">Online sessions for schools</h3>
    <div class="txt" style="left:183px;top:1576px;width:118px;font-size:3.9px">
      <p>Home learning during lockdown takes its toll on everyone- kids, parents &amp; teachers. If you want to schedule in a little chill out time between lessons, or at the end of a structured day of learning, I will teach a class that is tailored to your group's age &amp; needs. They don't even need to look at the screen the whole time!</p>
      <p>Options for:<br>- Preschool &amp; Prep<br>- Primary School<br>- High School</p>
    </div>
    <p class="a" style="left:183px;top:1650px;width:120px;font-size:4.6px;font-weight:700;color:#222;line-height:1.3">Yes! Our kids would benefit from some chill out time</p>
    <span class="btn" style="left:183px;top:1673px">Enquire Now</span>

    <footer class="footer" style="top:1713px">
      <h4 style="left:37px">Contact Us</h4>
      <ul style="left:37px"><li>Contact: Dana Whitfield</li><li>Phone: 0491 570 156</li><li>Email: info@openharboryoga.com.au</li><li>Location: Fernvale, Victoria Australia 3999</li></ul>
      <div class="f-mark">OpenHarbor Yoga</div>
      <h4 style="left:213px">Connect With Us</h4>
      <ul style="left:213px"><li>Facebook: OpenHarbor Yoga | Facebook</li><li>Instagram: openharboryoga4kids</li><li style="margin-top:4px">ABN: 12 345 678 901</li></ul>
      <div class="rule"></div><div class="copy">Copyright 2023 OpenHarbor Yoga</div>
    </footer>
  </section>

  <!-- BLOG -->
  <section class="page" style="left:930px;height:1064px;background:var(--grey)">
    <div class="topbar"><span>info@openharboryoga.com.au</span><span>Call Us: 0491 570 156</span><i class="dot"></i><i class="dot"></i></div>
    <nav class="nav"><div class="brand"><i></i>OpenHarbor Yoga</div><div class="menu"><span>Home</span><span>About</span><span>Classes</span><span class="on">Blog</span><span>Contact</span></div><span class="pill">Enquire Now</span></nav>
    <header class="hero" style="height:132px">
      <div class="hero-mark" style="top:14px;left:36px;width:100px;height:100px">OpenHarbor Yoga</div>
      <h1 style="top:54px;left:148px;font-size:15px">OpenHarbor Yoga Blog</h1>
    </header>
    <h2 class="h-sec" style="left:30px;top:202px;color:var(--title-ink)">Latest Blog Posts</h2>

    <article class="card" style="left:32px;top:235px;width:171px;height:120px">
      <div class="photo p-bright" role="img" aria-label="Group yoga class in a colourful studio" style="left:8px;top:12px;width:50px;height:44px"></div>
      <h3 style="left:66px;top:15px;width:100px">Lorem ipsum dolor sit ame consectetur adipiscinlore elised do eiusmod</h3>
      <div class="meta" style="left:100px;top:46px">Aug 06, 2023 &nbsp; 2 &nbsp; 947</div>
      <p class="txt" style="left:10px;top:66px;width:155px;font-size:3.7px">Lorem ipsum dolor sit amet, consectetur adipiscing elit, sed do eiusmod tempor incididunt ut labore et dolore magna aliqua. Quis ipsum susp endisse ultrices gravidasus commodo viverra maecen.</p>
      <div class="avatar" style="left:10px;top:93px"></div><div class="by" style="left:32px;top:96px">Admin by<br><b>Dana Whitfield</b></div>
      <span class="btn cy" style="left:114px;top:98px;font-size:3.8px;padding:2.5px 5px">Continue Reading</span>
    </article>
    <article class="card" style="left:32px;top:368px;width:171px;height:120px">
      <div class="photo p-room" role="img" aria-label="Instructor doing a downward dog pose" style="left:8px;top:12px;width:50px;height:44px"></div>
      <h3 style="left:66px;top:15px;width:100px">Lorem ipsum dolor sit ame consectetur adipiscinlore elised do eiusmod</h3>
      <div class="meta" style="left:100px;top:46px">Aug 06, 2023 &nbsp; 2 &nbsp; 947</div>
      <p class="txt" style="left:10px;top:66px;width:155px;font-size:3.7px">Lorem ipsum dolor sit amet, consectetur adipiscing elit, sed do eiusmod tempor incididunt ut labore et dolore magna aliqua. Quis ipsum susp endisse ultrices gravidasus commodo viverra maecen.</p>
      <div class="avatar" style="left:10px;top:93px"></div><div class="by" style="left:32px;top:96px">Admin by<br><b>Dana Whitfield</b></div>
      <span class="btn cy" style="left:114px;top:98px;font-size:3.8px;padding:2.5px 5px">Continue Reading</span>
    </article>
    <article class="card" style="left:32px;top:502px;width:171px;height:120px">
      <div class="photo p-warm" role="img" aria-label="Pair doing a partner yoga pose" style="left:8px;top:12px;width:50px;height:44px"></div>
      <h3 style="left:66px;top:15px;width:100px">Lorem ipsum dolor sit ame consectetur adipiscinlore elised do eiusmod</h3>
      <div class="meta" style="left:100px;top:46px">Aug 06, 2023 &nbsp; 2 &nbsp; 947</div>
      <p class="txt" style="left:10px;top:66px;width:155px;font-size:3.7px">Lorem ipsum dolor sit amet, consectetur adipiscing elit, sed do eiusmod tempor incididunt ut labore et dolore magna aliqua. Quis ipsum susp endisse ultrices gravidasus commodo viverra maecen.</p>
      <div class="avatar" style="left:10px;top:93px"></div><div class="by" style="left:32px;top:96px">Admin by<br><b>Dana Whitfield</b></div>
      <span class="btn cy" style="left:114px;top:98px;font-size:3.8px;padding:2.5px 5px">Continue Reading</span>
    </article>
    <article class="card" style="left:32px;top:635px;width:171px;height:120px">
      <div class="photo p-kids" role="img" aria-label="Child stretching on a pink mat" style="left:8px;top:12px;width:50px;height:44px"></div>
      <h3 style="left:66px;top:15px;width:100px">Lorem ipsum dolor sit ame consectetur adipiscinlore elised do eiusmod</h3>
      <div class="meta" style="left:100px;top:46px">Aug 06, 2023 &nbsp; 2 &nbsp; 947</div>
      <p class="txt" style="left:10px;top:66px;width:155px;font-size:3.7px">Lorem ipsum dolor sit amet, consectetur adipiscing elit, sed do eiusmod tempor incididunt ut labore et dolore magna aliqua. Quis ipsum susp endisse ultrices gravidasus commodo viverra maecen.</p>
      <div class="avatar" style="left:10px;top:93px"></div><div class="by" style="left:32px;top:96px">Admin by<br><b>Dana Whitfield</b></div>
      <span class="btn cy" style="left:114px;top:98px;font-size:3.8px;padding:2.5px 5px">Continue Reading</span>
    </article>
    <article class="card" style="left:32px;top:768px;width:171px;height:120px">
      <div class="photo p-bright" role="img" aria-label="Kids yoga class with arms raised" style="left:8px;top:12px;width:50px;height:44px"></div>
      <h3 style="left:66px;top:15px;width:100px">Lorem ipsum dolor sit ame consectetur adipiscinlore elised do eiusmod</h3>
      <div class="meta" style="left:100px;top:46px">Aug 06, 2023 &nbsp; 2 &nbsp; 947</div>
      <p class="txt" style="left:10px;top:66px;width:155px;font-size:3.7px">Lorem ipsum dolor sit amet, consectetur adipiscing elit, sed do eiusmod tempor incididunt ut labore et dolore magna aliqua. Quis ipsum susp endisse ultrices gravidasus commodo viverra maecen.</p>
      <div class="avatar" style="left:10px;top:93px"></div><div class="by" style="left:32px;top:96px">Admin by<br><b>Dana Whitfield</b></div>
      <span class="btn cy" style="left:114px;top:98px;font-size:3.8px;padding:2.5px 5px">Continue Reading</span>
    </article>
    <div class="a" style="left:80px;top:908px;font-size:5px;color:#333">Page 1 of 3</div>
    <span class="btn cy" style="left:122px;top:905px;font-family:Arimo,sans-serif">Next</span>

    <aside class="side">
      <h5 style="left:226px;top:233px">Recent Posts</h5>
      <div class="rp" style="left:227px;top:257px"><div class="photo p-warm" role="img" aria-label="Yoga class thumbnail"></div><div class="t">Lorem ipsum dolor sit amet, consectetur loremadlisi<span>August 11, 2023</span></div></div>
      <div class="rp" style="left:227px;top:290px"><div class="photo p-dark" role="img" aria-label="Yoga pose thumbnail"></div><div class="t">Lorem ipsum dolor sit amet, consectetur loremadlisi<span>August 11, 2023</span></div></div>
      <div class="rp" style="left:227px;top:323px"><div class="photo p-bright" role="img" aria-label="Outdoor yoga thumbnail"></div><div class="t">Lorem ipsum dolor sit amet, consectetur loremadlisi<span>August 11, 2023</span></div></div>
      <div class="rp" style="left:227px;top:356px"><div class="photo p-mat" role="img" aria-label="Stretching thumbnail"></div><div class="t">Lorem ipsum dolor sit amet, consectetur loremadlisi<span>August 11, 2023</span></div></div>
      <h5 style="left:226px;top:408px">Advertising</h5>
      <div class="photo p-kids" role="img" aria-label="Group of smiling children holding yoga mats" style="left:227px;top:430px;width:83px;height:115px"><div class="ad-cap">Lorem ipsum dolor sit amet, consectetur adipiscing elit, sed do eiusmod temp</div></div>
    </aside>

    <footer class="footer" style="top:957px;height:107px">
      <h4 style="left:37px">Contact Us</h4>
      <ul style="left:37px"><li>Contact: Dana Whitfield</li><li>Phone: 0491 570 156</li><li>Email: info@openharboryoga.com.au</li><li>Location: Fernvale, Victoria Australia 3999</li></ul>
      <div class="f-mark">OpenHarbor Yoga</div>
      <h4 style="left:213px">Connect With Us</h4>
      <ul style="left:213px"><li>Facebook: OpenHarbor Yoga | Facebook</li><li>Instagram: openharboryoga4kids</li><li style="margin-top:4px">ABN: 12 345 678 901</li></ul>
      <div class="copy" style="top:88px">Copyright 2023 OpenHarbor Yoga</div>
    </footer>
  </section>

  <!-- SINGLE BLOG -->
  <section class="page" style="left:1344px;height:1008px;background:var(--grey)">
    <div class="topbar"><span>info@openharboryoga.com.au</span><span>Call Us: 0491 570 156</span><i class="dot"></i><i class="dot"></i></div>
    <nav class="nav"><div class="brand"><i></i>OpenHarbor Yoga</div><div class="menu"><span>Home</span><span>About</span><span>Classes</span><span class="on">Blog</span><span>Contact</span></div><span class="pill">Enquire Now</span></nav>
    <header class="hero" style="height:132px">
      <div class="hero-mark" style="top:14px;left:36px;width:100px;height:100px">OpenHarbor Yoga</div>
      <h1 style="top:54px;left:148px;font-size:15px">OpenHarbor Yoga Blog</h1>
    </header>

    <article class="card" style="left:30px;top:210px;width:183px;height:475px">
      <h3 style="left:11px;top:14px;width:165px;font-size:8.6px">Lorem ipsum dolor sit ametlol cons ectetur adipiscing elitlorem.</h3>
      <div class="photo p-room" role="img" aria-label="Row of people standing on yoga mats" style="left:11px;top:40px;width:162px;height:99px"></div>
      <div class="meta" style="left:11px;top:145px;font-weight:700;color:#333">Apr 30, 2023 &nbsp;·&nbsp; 1 min read &nbsp;&nbsp;&nbsp; 2 &nbsp;&nbsp; 947 &nbsp;&nbsp; Admin</div>
      <p class="txt" style="left:11px;top:158px;width:162px;font-size:3.6px">Lorem ipsum dolor sit amet,consec tetur adi piscing elit, sed do usmod tempor incididunt utlorell dolore magna aliqua. Lorem ipsum dolor sit amet,consec tetur adi piscing elit, sed do usmod tempor incididunt ut lab ore dolore magna aliqua. Sed ut perspiciatis unde omnis iste natus error sit voluptatem accusantium doloremque laudantium, totam rem aperiam, eaque ipsa quae ab illo inventore veritatis et quasi architecto beatae vitae dicta sunt explicabo. Nemo enim ipsam voluptatem quia voluptas sit asp ernatur aut odit aut fugit, sed quia consequuntur magni dolores eos qui ratione voluptatem sequi nesciunt. Neque porro quisquam est, qui dolor em ipsum quia dolor sit amet, consectetur, adipisci velit, sed quia non numquam eius modi tempora incidunt ut labore et dolore magnam aliqu am quaerat voluptatem.</p>
      <div class="photo p-kids" role="img" aria-label="Smiling girl sitting on a yoga mat in class" style="left:11px;top:240px;width:162px;height:97px"></div>
      <h3 style="left:11px;top:349px;width:165px;font-size:8.6px">Lorem ipsum dolor sit ametlol cons ectetur adipiscing elitlorem.</h3>
      <p class="txt" style="left:11px;top:375px;width:162px;font-size:3.6px">Lorem ipsum dolor sit amet,consec tetur adi piscing elit, sed do usmod tem por incididunt utlorell dolore magna aliqua. Lorem ipsum dolor sit amet consec tetur adi piscing elit, sed do usmod tempor incididunt ut lab ore dolore magna aliqua. Sed ut perspiciatis unde omnis iste natus error sit voluptatem accusantium doloremque laudantium, totam rem aperiam, eaque ipsa quae ab illo inventore veritatis et quasi architecto beatae vitae dicta sunt explicabo. Nemo enim ipsam voluptatem quia voluptas sit asp ernatur aut odit aut fugit, sed quia consequuntur magni dolores eos q.</p>
      <div class="a" style="left:11px;top:437px;width:162px;border-top:.6px solid #ccc"></div>
      <div class="a" style="left:11px;top:448px;font-size:5px;color:#333">Share Article:</div>
      <span class="share" style="left:60px;top:445px;background:#2d5fb5"></span>
      <span class="share" style="left:80px;top:445px;background:#1da1f2"></span>
      <span class="share" style="left:100px;top:445px;background:#e0405a"></span>
      <span class="share" style="left:120px;top:445px;background:#2cb96b"></span>
    </article>

    <section class="card" style="left:30px;top:700px;width:183px;height:190px">
      <div class="a" style="left:11px;top:16px;font-size:5.4px;font-weight:700;color:var(--title-ink)">Leave a Reply</div>
      <div class="a" style="left:46px;top:19px;width:126px;border-top:.6px solid var(--blue)"></div>
      <div class="input" style="left:11px;top:30px;width:162px;height:42px">Comment</div>
      <div class="input" style="left:11px;top:76px;width:98px;height:10px">Name</div>
      <div class="input" style="left:98px;top:76px;width:75px;height:10px">Email</div>
      <div class="input" style="left:11px;top:93px;width:162px;height:10px">Website</div>
      <div class="a" style="left:11px;top:111px;width:5px;height:5px;border:.6px solid #999"></div>
      <div class="a" style="left:19px;top:111px;font-size:3.5px;color:#666;white-space:nowrap">Save my name, email, and website in this browser for the next time I comment.</div>
      <span class="btn" style="left:11px;top:126px;font-size:5.5px;padding:4px 13px">Post Comment</span>
    </section>

    <aside class="side">
      <h5 style="left:226px;top:233px">Recent Posts</h5>
      <div class="rp" style="left:227px;top:257px"><div class="photo p-warm" role="img" aria-label="Yoga class thumbnail"></div><div class="t">Lorem ipsum dolor sit amet, consectetur loremadlisi<span>August 11, 2023</span></div></div>
      <div class="rp" style="left:227px;top:290px"><div class="photo p-dark" role="img" aria-label="Yoga pose thumbnail"></div><div class="t">Lorem ipsum dolor sit amet, consectetur loremadlisi<span>August 11, 2023</span></div></div>
      <div class="rp" style="left:227px;top:323px"><div class="photo p-bright" role="img" aria-label="Outdoor yoga thumbnail"></div><div class="t">Lorem ipsum dolor sit amet, consectetur loremadlisi<span>August 11, 2023</span></div></div>
      <div class="rp" style="left:227px;top:356px"><div class="photo p-mat" role="img" aria-label="Stretching thumbnail"></div><div class="t">Lorem ipsum dolor sit amet, consectetur loremadlisi<span>August 11, 2023</span></div></div>
      <h5 style="left:226px;top:408px">Advertising</h5>
      <div class="photo p-kids" role="img" aria-label="Group of smiling children holding yoga mats" style="left:227px;top:430px;width:83px;height:115px"><div class="ad-cap">Lorem ipsum dolor sit amet, consectetur adipiscing elit, sed do eiusmod temp</div></div>
    </aside>

    <footer class="footer" style="top:903px;height:105px">
      <h4 style="left:37px">Contact Us</h4>
      <ul style="left:37px"><li>Contact: Dana Whitfield</li><li>Phone: 0491 570 156</li><li>Email: info@openharboryoga.com.au</li><li>Location: Fernvale, Victoria Australia 3999</li></ul>
      <div class="f-mark">OpenHarbor Yoga</div>
      <h4 style="left:213px">Connect With Us</h4>
      <ul style="left:213px"><li>Facebook: OpenHarbor Yoga | Facebook</li><li>Instagram: openharboryoga4kids</li><li style="margin-top:4px">ABN: 12 345 678 901</li></ul>
      <div class="copy" style="top:86px">Copyright 2023 OpenHarbor Yoga</div>
    </footer>
  </section>

</div>
</body>
</html>
```